Business Card Design for company

We want new business cards. We'd like something different-- yet still highly professional. Our tagline is Providing leadership, delivering success. Stock photos are ok, as long as they are relevant and look upscale.

Target Market(s)

Architecture/Business Management Consulting/Engineering Consulting

Contact Information for Business Card

dark gray background with pops of blue might be good, but you tell me. You're the designers. Rounded corners might be nice, but again, you tell me.

Font styles to use
Serif
Sans Serif

Colors
3276b5
5c5c5c
9d9d9d
fbfbfb

Requirements
Nice to have
• Something different, but still very professional.

```html
<!DOCTYPE html>
<html lang="en">
<head>
<meta charset="utf-8">
<title>Norvale International – Business Card</title>
<link rel="stylesheet" href="https://fonts.googleapis.com/css2?family=Montserrat:wght@400;500;700&display=swap">
<style>
  :root {
    --brand-blue: #3276b5;
    --brand-gray: #5c5c5c;
    --light-gray: #9d9d9d;
    --paper-white: #fbfbfb;
    --card-black: #0b0c0e;
    --map-tone: #1a1c20;
    --stage: #1d1e21;
  }
  * { box-sizing: border-box; margin: 0; padding: 0; }
  html, body { width: 1200px; height: 900px; overflow: hidden; }
  body {
    background: var(--stage);
    font-family: "Montserrat", Arial, sans-serif;
    color: var(--paper-white);
    position: relative;
  }
  .card {
    position: absolute;
    left: 320px;
    width: 560px;
    height: 320px;
    background: var(--card-black);
    border-radius: 8px;
    overflow: hidden;
    box-shadow: 0 12px 30px rgba(0,0,0,.5);
  }
  .card--front { top: 110px; }
  .card--back { top: 470px; }

  .world-map {
    position: absolute;
    inset: 20px 30px 40px 30px;
    border-radius: 40%;
    background: radial-gradient(ellipse at center, var(--map-tone) 0%, rgba(26,28,32,0) 70%);
  }

  /* Front */
  .front-brand {
    position: absolute;
    left: 0; right: 0; top: 78px;
    text-align: center;
  }
  .brand-name {
    font-weight: 700;
    color: var(--brand-blue);
    letter-spacing: 6px;
  }
  .front-brand .brand-name { font-size: 52px; line-height: 1; }
  .brand-sub {
    font-weight: 500;
    color: var(--paper-white);
    letter-spacing: 4px;
  }
  .front-brand .brand-sub { font-size: 24px; margin-top: 8px; }
  .tagline {
    position: absolute;
    left: 0; right: 0; top: 218px;
    text-align: center;
    font-size: 10px;
    letter-spacing: 1.6px;
    line-height: 1.7;
    text-transform: uppercase;
  }

  /* Back */
  .back-brand {
    position: absolute;
    left: 40px; top: 92px;
    width: 220px;
    text-align: center;
  }
  .back-brand .brand-name { font-size: 30px; line-height: 1; }
  .back-brand .brand-sub { font-size: 15px; margin-top: 6px; color: var(--light-gray); letter-spacing: 3px; }
  .divider {
    position: absolute;
    left: 282px; top: 48px;
    width: 1px; height: 150px;
    background: var(--light-gray);
  }
  .contact {
    position: absolute;
    left: 306px; top: 52px;
  }
  .contact-name { font-size: 17px; font-weight: 700; letter-spacing: 1px; }
  .contact-title { font-size: 10px; color: var(--paper-white); margin-top: 3px; letter-spacing: .5px; }
  .contact-list { list-style: none; margin-top: 14px; font-size: 10px; line-height: 1.75; }
  .contact-list li { display: flex; align-items: center; gap: 8px; }
  .contact-list svg { width: 9px; height: 9px; fill: none; stroke: var(--paper-white); stroke-width: 1.4; }
  .address-band {
    position: absolute;
    left: 0; right: 0; bottom: 0;
    height: 46px;
    background: var(--brand-blue);
    border-top: 3px solid var(--card-black);
    box-shadow: 0 -2px 0 var(--brand-blue);
    display: flex; align-items: center; justify-content: center;
    font-size: 12px;
    letter-spacing: .5px;
    color: var(--paper-white);
  }
</style>
</head>
<body>
  <section class="card card--front">
    <div class="world-map" role="img" aria-label="Faint world map in dark gray"></div>
    <div class="front-brand">
      <div class="brand-name">NORVALE</div>
      <div class="brand-sub">INTERNATIONAL</div>
    </div>
    <p class="tagline">Guiding projects | Building lasting results<br>Independent project delivery consultants since 2006</p>
  </section>

  <section class="card card--back">
    <div class="world-map" role="img" aria-label="Dotted world map in dark gray"></div>
    <div class="back-brand">
      <div class="brand-name">NORVALE</div>
      <div class="brand-sub">INTERNATIONAL</div>
    </div>
    <div class="divider"></div>
    <div class="contact">
      <div class="contact-name">DANIEL HART</div>
      <div class="contact-title">Design Consultant</div>
      <ul class="contact-list">
        <li><svg viewBox="0 0 10 10"><path d="M2 1 L4 1 L4.5 3 L3.5 4 Q4.5 6 6 6.5 L7 5.5 L9 6 L9 8 Q5 9 2 5 Q1 3 2 1Z"/></svg>+1 555-010-4821</li>
        <li><svg viewBox="0 0 10 10"><rect x="1" y="2" width="8" height="6"/><path d="M1 2 L5 5.5 L9 2"/></svg>MARKETING@NORVALEINTL.COM</li>
        <li><svg viewBox="0 0 10 10"><rect x="1" y="2" width="8" height="6"/><path d="M1 2 L5 5.5 L9 2"/></svg>INFO@NORVALEINTL.COM</li>
        <li><svg viewBox="0 0 10 10"><circle cx="5" cy="5" r="4"/><path d="M1 5 H9 M5 1 Q2.5 5 5 9 M5 1 Q7.5 5 5 9"/></svg>www.norvaleintl.com</li>
      </ul>
    </div>
    <div class="address-band">4180 Cedar Point Drive Orlando, FL 32801</div>
  </section>
</body>
</html>
```